Business Card For Halvenmoor Financial Consulting

Hi, I would like a business card designed. Bold, modern.
Please use the same design as the logo. I have also attached the website design to see the overall theme.
Wordmark Font
Color: Hex: #01AEF7

```html
<!DOCTYPE html>
<html lang="en">
<head>
<meta charset="utf-8">
<title>Halvenmoor Financial Consulting – Business Card</title>
<link rel="stylesheet" href="https://fonts.googleapis.com/css2?family=Open+Sans:wght@400;600;700&display=swap">
<style>
  :root {
    --navy: #14202b;
    --navy-deep: #0f1922;
    --brand-blue: #01aef7;
    --blue-mid: #1f86b8;
    --blue-dark: #0f5477;
    --ink: #14202b;
    --paper-text: #ffffff;
    --backdrop: #6b6e72;
  }
  * { margin: 0; padding: 0; box-sizing: border-box; }
  html, body { width: 1200px; height: 900px; overflow: hidden; }
  body {
    background: var(--backdrop);
    font-family: "Open Sans", Arial, sans-serif;
    position: relative;
  }
  .card {
    position: absolute;
    top: 118px;
    width: 380px;
    height: 665px;
    background: var(--navy);
    overflow: hidden;
    box-shadow: 0 14px 30px rgba(0,0,0,.35);
  }
  .card--front { left: 170px; }
  .card--back { left: 650px; }
  .card__shapes { position: absolute; inset: 0; width: 100%; height: 100%; }

  /* Front */
  .brand {
    position: absolute;
    top: 92px;
    left: 0;
    width: 100%;
    text-align: center;
    color: var(--paper-text);
  }
  .brand__mark {
    display: block;
    width: 34px;
    height: 34px;
    margin: 0 auto 18px;
    background: var(--brand-blue);
  }
  .brand__name {
    font-weight: 700;
    font-size: 30px;
    letter-spacing: 1px;
    line-height: 1.15;
    text-transform: uppercase;
  }
  .brand__name span { display: block; font-size: 15px; letter-spacing: 9px; }

  .contact {
    position: absolute;
    right: 26px;
    top: 392px;
    text-align: right;
    color: var(--paper-text);
  }
  .contact__name {
    color: var(--ink);
    font-weight: 700;
    font-size: 22px;
    line-height: 1;
  }
  .contact__title { font-size: 15px; margin-bottom: 22px; }
  .contact__row {
    display: flex;
    justify-content: flex-end;
    align-items: center;
    gap: 7px;
    font-size: 13.5px;
    line-height: 25px;
  }
  .contact__row svg { width: 14px; height: 14px; fill: var(--ink); flex: none; }
  .contact__rule {
    height: 1px;
    background: var(--ink);
    margin: 8px 0 8px 20px;
    opacity: .8;
  }
  .contact__address { display: flex; justify-content: flex-end; gap: 7px; font-size: 14px; line-height: 20px; }
  .contact__address svg { width: 14px; height: 18px; fill: var(--ink); flex: none; margin-top: 2px; }

  /* Back */
  .back-wordmark {
    position: absolute;
    left: 70px;
    top: 300px;
    writing-mode: vertical-rl;
    color: var(--ink);
    font-weight: 700;
    text-transform: uppercase;
    line-height: 1;
  }
  .back-wordmark__main { font-size: 44px; letter-spacing: 2px; }
  .back-wordmark__sub { font-size: 18px; letter-spacing: 12px; margin-right: 10px; }
  .back-url {
    position: absolute;
    right: 22px;
    top: 28px;
    writing-mode: vertical-rl;
    color: var(--paper-text);
    font-size: 14px;
    letter-spacing: 4px;
  }
</style>
</head>
<body>

<section class="card card--front" aria-label="Business card front">
  <svg class="card__shapes" viewBox="0 0 380 665" preserveAspectRatio="none" aria-hidden="true">
    <defs>
      <linearGradient id="frontBlue" x1="0" y1="0" x2="1" y2="1">
        <stop offset="0" stop-color="#0f5477"/>
        <stop offset=".55" stop-color="#1f86b8"/>
        <stop offset="1" stop-color="#0f5477"/>
      </linearGradient>
    </defs>
    <polygon points="0,590 380,115 380,665 0,665" fill="url(#frontBlue)"/>
    <polygon points="0,590 380,115 380,124 10,590" fill="#01aef7" opacity=".55"/>
  </svg>

  <div class="brand">
    <span class="brand__mark"></span>
    <div class="brand__name">Halvenmoor<span>Consulting</span></div>
  </div>

  <div class="contact">
    <div class="contact__name">MARA ELLISON</div>
    <div class="contact__title">Manager</div>
    <div class="contact__row">(025) 418 20573
      <svg viewBox="0 0 24 24"><path d="M6.6 10.8a15 15 0 0 0 6.6 6.6l2.2-2.2c.3-.3.7-.4 1-.2 1.1.4 2.3.6 3.6.6.6 0 1 .4 1 1V20c0 .6-.4 1-1 1A17 17 0 0 1 3 4c0-.6.4-1 1-1h3.5c.6 0 1 .4 1 1 0 1.3.2 2.5.6 3.6.1.3 0 .7-.2 1z"/></svg>
    </div>
    <div class="contact__row">info@halvenmoorconsulting.com
      <svg viewBox="0 0 24 24"><path d="M2 5h20v14H2zm2 2v.5l8 5 8-5V7l-8 5z"/></svg>
    </div>
    <div class="contact__row">www.halvenmoorconsulting.com
      <svg viewBox="0 0 24 24"><path d="M12 2a10 10 0 1 0 0 20 10 10 0 0 0 0-20zm0 2c.9 1.2 1.6 2.6 2 4h-4c.4-1.4 1.1-2.8 2-4zM4.3 14a8 8 0 0 1 0-4h3.4a16 16 0 0 0 0 4zm5.4 0a14 14 0 0 1 0-4h4.6a14 14 0 0 1 0 4zm6.6 0a16 16 0 0 0 0-4h3.4a8 8 0 0 1 0 4zM10 16h4c-.4 1.4-1.1 2.8-2 4-.9-1.2-1.6-2.6-2-4z"/></svg>
    </div>
    <div class="contact__rule"></div>
    <div class="contact__address">
      <span>2718 Larkspur Avenue<br>Bellhaven, FL 32145</span>
      <svg viewBox="0 0 24 30"><path d="M12 0a9 9 0 0 0-9 9c0 7 9 17 9 17s9-10 9-17a9 9 0 0 0-9-9zm0 13a4 4 0 1 1 0-8 4 4 0 0 1 0 8z"/></svg>
    </div>
  </div>
</section>

<section class="card card--back" aria-label="Business card back">
  <svg class="card__shapes" viewBox="0 0 380 665" preserveAspectRatio="none" aria-hidden="true">
    <defs>
      <linearGradient id="backBlue" x1="0" y1="0" x2="1" y2="1">
        <stop offset="0" stop-color="#0f5477"/>
        <stop offset=".5" stop-color="#1f86b8"/>
        <stop offset="1" stop-color="#0f5477"/>
      </linearGradient>
    </defs>
    <polygon points="0,140 380,500 380,665 0,665" fill="url(#backBlue)"/>
    <polygon points="0,140 380,500 380,510 0,150" fill="#01aef7" opacity=".55"/>
  </svg>

  <div class="back-wordmark">
    <span class="back-wordmark__main">Halvenmoor</span>
    <span class="back-wordmark__sub">Consulting</span>
  </div>

  <div class="back-url">www.halvenmoorconsulting.com</div>
</section>

</body>
</html>
```